Youth Lifting Youth Business Card. We have existing logo

We need a business card design from an existing logo.
Our logo is in black and white but would love to add in the color burgundy but we're open to any color. Our website is www.youthliftingyouthmv.org

Target Market(s)

corporations and foundations who will be donating

Industry/Entity Type

Business

Contact Information for Business Card

Address: 2318 Marwick Ave Santa Barbara, CA 93110
Name: Corin Halvorsen
Founder email: corin.halvorsen@youthliftingyouthmv.org
Phone: 805-637-9081

Requirements
Nice to have
• Our colors are burgundy and white, but that's not a necessity

```html
<!DOCTYPE html>
<html lang="en">
<head>
<meta charset="utf-8">
<title>Youth Lifting Youth – Business Card</title>
<link rel="stylesheet" href="https://fonts.googleapis.com/css2?family=Arimo:wght@400&display=swap">
<style>
  :root {
    --page-bg: #d9d4cc;
    --panel-dark: #1f1f1f;
    --panel-mid: #3a3a3a;
    --card-light: #e6e2dc;
    --card-light-2: #d6dbe0;
    --ink: #141414;
    --rule: #4a4a4a;
    --icon-line: #f2f2f2;
    --logo-ink: #f0f0f0;
  }
  * { box-sizing: border-box; margin: 0; padding: 0; }
  html, body {
    width: 1200px; height: 970px; overflow: hidden;
    background: var(--page-bg);
    font-family: "Arimo", Arial, sans-serif;
  }
  .card {
    position: absolute; left: 100px; top: 207px;
    width: 1000px; height: 555px;
    background: linear-gradient(135deg, var(--card-light) 0%, var(--card-light) 55%, var(--card-light-2) 100%);
    border: 1px solid #b9b5ae;
    overflow: hidden;
  }
  .brand-panel {
    position: absolute; left: 0; top: 0; width: 400px; height: 100%;
    background: radial-gradient(ellipse at 45% 30%, var(--panel-mid) 0%, var(--panel-dark) 65%, #2c2c2c 100%);
  }
  .brand-mark {
    position: absolute; left: 58px; top: 300px; width: 220px;
    display: flex; align-items: center; gap: 12px;
  }
  .brand-mark .dot {
    width: 26px; height: 26px; border-radius: 50%;
    background: var(--logo-ink); flex: none;
  }
  .brand-mark .brand-name {
    color: var(--logo-ink); font-size: 24px; line-height: 1.2;
  }
  .identity {
    position: absolute; left: 420px; top: 132px;
    border-left: 2px solid var(--ink); padding-left: 18px;
  }
  .identity .name { font-size: 45px; color: var(--ink); line-height: 1; }
  .identity .role { font-size: 22px; color: var(--ink); margin-top: 6px; }
  .rules { position: absolute; left: 400px; top: 0; width: 600px; height: 100%; }
  .rule { position: absolute; left: 0; width: 100%; height: 1.5px; background: var(--rule); }
  .contact-icon {
    position: absolute; left: 335px; width: 40px; height: 40px;
  }
  .contact-text {
    position: absolute; left: 418px; font-size: 23px; color: var(--ink); line-height: 1;
  }
</style>
</head>
<body>
  <main class="card">
    <section class="brand-panel">
      <div class="brand-mark">
        <span class="dot"></span>
        <span class="brand-name">Youth Lifting Youth</span>
      </div>
    </section>

    <div class="identity">
      <div class="name">Corin Halvorsen</div>
      <div class="role">Founder</div>
    </div>

    <div class="rules">
      <span class="rule" style="top:302px"></span>
      <span class="rule" style="top:352px"></span>
      <span class="rule" style="top:361px"></span>
      <span class="rule" style="top:409px"></span>
      <span class="rule" style="top:418px"></span>
      <span class="rule" style="top:468px"></span>
    </div>

    <svg class="contact-icon" style="top:307px" viewBox="0 0 40 40" aria-hidden="true">
      <circle cx="20" cy="20" r="18" fill="none" stroke="var(--icon-line)" stroke-width="2"/>
      <path d="M14 11c1-1 2-1 3 0l2 3c.5 1 .3 1.7-.5 2.3l-1 .8c.8 2 2.4 3.6 4.4 4.4l.8-1c.6-.8 1.3-1 2.3-.5l3 2c1 1 1 2 0 3l-1.5 1.5c-1 1-3 1-5.5-.5-3-1.8-6-4.8-7.8-7.8-1.5-2.5-1.5-4.5-.5-5.5z" fill="var(--icon-line)"/>
    </svg>
    <div class="contact-text" style="top:316px">805-637-9081</div>

    <svg class="contact-icon" style="top:365px" viewBox="0 0 40 40" aria-hidden="true">
      <circle cx="20" cy="20" r="18" fill="none" stroke="var(--icon-line)" stroke-width="2"/>
      <rect x="11" y="14" width="18" height="12" rx="1.5" fill="var(--icon-line)"/>
      <path d="M11.5 14.8l8.5 6 8.5-6" fill="none" stroke="var(--panel-dark)" stroke-width="1.5"/>
    </svg>
    <div class="contact-text" style="top:373px">corin.halvorsen@youthliftingyouthmv.org</div>

    <svg class="contact-icon" style="top:421px" viewBox="0 0 40 40" aria-hidden="true">
      <circle cx="20" cy="20" r="18" fill="none" stroke="var(--icon-line)" stroke-width="2"/>
      <path d="M20 10c-4 0-7 3-7 7 0 5 7 13 7 13s7-8 7-13c0-4-3-7-7-7z" fill="var(--icon-line)"/>
      <circle cx="20" cy="17" r="2.6" fill="var(--panel-dark)"/>
    </svg>
    <div class="contact-text" style="top:431px">2318 Marwick Ave Santa Barbara, CA 93110</div>
  </main>
</body>
</html>
```